Website for Torvel Capital - investment banking firm

We have a corporate identity (thanks to Ravinka/31842) and want to extend that into a website design.  See the attached zipped files.
We have software folks in-house to do the coding.
See the attached Project Brief & Notes for more details.  Don't worry about the actual text - lorem ipsum will be fine.
The server will be Apache.
Thank you!
Desmond

Industry/Entity Type
Investment

```html
<!DOCTYPE html>
<html lang="en">
<head>
<meta charset="utf-8">
<title>Torvel Capital</title>
<link href="https://fonts.googleapis.com/css2?family=Cinzel:wght@400;600;700&family=Lato:ital,wght@0,400;0,700;1,400&family=Open+Sans:wght@400&display=swap" rel="stylesheet">
<style>
:root{
  --navy:#163d7c;
  --navy-deep:#0b3572;
  --blue:#1f4f96;
  --blue-light:#5a9ad3;
  --dark:#333;
  --rule:#cfd3d8;
  --bubble:#e3e5e8;
  --white:#fff;
}
*{box-sizing:border-box;margin:0;padding:0}
html,body{width:1200px;height:1148px;overflow:hidden}
body{position:relative;background:var(--white);font-family:'Lato',sans-serif;color:var(--dark)}
.abs{position:absolute}
.header{left:0;top:0;width:1200px;height:95px;background:var(--white)}
.follow{left:131px;top:38px;font-family:'Cinzel',serif;font-weight:700;color:var(--navy);font-size:20px;display:flex;align-items:center;gap:8px}
.follow .social{width:26px;height:26px;border-radius:50%;background:#8b8b8b;display:inline-block}
.logo{left:431px;top:16px;display:flex;align-items:center;gap:14px}
.logo .mark{width:52px;height:52px;background:var(--navy)}
.logo .name{font-family:'Cinzel',serif;font-weight:600;font-size:32px;color:var(--navy);border-left:2px solid #777;padding-left:14px;line-height:64px;white-space:nowrap}
.contact-top{left:848px;top:29px;display:flex;gap:12px;align-items:center}
.contact-top .ring{width:40px;height:40px;border:2px solid #444;border-radius:50%;display:flex;align-items:center;justify-content:center}
.contact-top .q{font-family:'Cinzel',serif;font-weight:700;color:var(--navy);font-size:15px;line-height:16px;white-space:nowrap}
.contact-top .num{font-family:'Cinzel',serif;font-size:25px;color:#444;line-height:28px;white-space:nowrap}
.nav{left:0;top:95px;width:1200px;height:41px;background:linear-gradient(#24549c,#163f80)}
.nav ul{position:absolute;left:131px;top:0;display:flex;list-style:none;height:41px}
.nav li{font-family:'Cinzel',serif;font-weight:600;color:var(--white);font-size:14.5px;line-height:41px;padding:0 17px;border-right:1px solid #0c2d62;text-transform:uppercase;white-space:nowrap}
.nav li.active{background:linear-gradient(#6aa6d8,#3b78ba);padding:0 24px}
.backdrop{left:0;top:136px;width:1200px;height:792px;background:linear-gradient(90deg,#e4e6e8,#f7f8f9 8%,#eef0f2 90%,#d8dbdf)}
.footer-band{left:0;top:928px;width:1200px;height:220px;background:var(--navy-deep)}
.page{left:131px;top:136px;width:938px;height:853px;background:var(--white)}
.hero{left:131px;top:136px;width:938px;height:516px;background:linear-gradient(180deg,#3f74b8 0%,#6e9fd2 45%,#a9c6e4 75%,#3d5576 100%)}
.hero-caption{left:131px;top:464px;width:502px;background:rgba(238,238,240,.9);padding:10px 17px 12px}
.hero-caption h1{font-family:'Cinzel',serif;font-weight:700;font-size:32px;color:var(--navy);line-height:44px;text-transform:uppercase;white-space:nowrap}
.hero-caption p{font-family:'Open Sans',sans-serif;font-size:18.5px;line-height:27px;color:#333;margin-top:2px}
.col-head{font-family:'Cinzel',serif;font-weight:600;font-size:19px;color:#333;line-height:30px;height:42px;border-bottom:1px solid var(--rule);white-space:nowrap}
.col-head span{color:var(--navy)}
.about{left:147px;top:683px;width:268px}
.photo{width:268px;height:103px;background:linear-gradient(90deg,#c8c9c4,#e6e1d6 40%,#3a3e46 70%,#d6d7d8);margin-top:11px}
.about p{font-size:13px;line-height:19.5px;letter-spacing:.2px;margin-top:9px;color:#333}
.more{font-size:13px;font-weight:700;color:#333;text-align:right;position:absolute;top:256px;right:0}
.divider{width:1px;height:230px;background:linear-gradient(transparent,#ddd,transparent)}
.services{left:473px;top:683px;width:265px}
.svc{display:flex;align-items:center;gap:12px;height:68px;border-bottom:2px solid #e4e5e7;font-weight:700;font-size:15px;color:#333;line-height:18px}
.svc svg{flex:none;border-right:1px solid #ccc;padding-right:8px;width:40px}
.testimonials{left:790px;top:683px;width:263px}
.bubble{background:var(--bubble);border-radius:10px;margin-top:14px;height:130px;padding:14px 6px 0 12px;font-style:italic;font-size:12.5px;line-height:22.5px;color:#333;position:relative}
.bubble:after{content:"";position:absolute;right:30px;bottom:-18px;border-left:34px solid transparent;border-top:18px solid var(--bubble)}
.client{display:flex;align-items:center;gap:12px;margin-top:-12px;margin-left:12px;position:relative}
.avatar{width:66px;height:66px;border-radius:5px;background:linear-gradient(#7a6a60,#40506a);border:2px solid var(--white);box-shadow:0 1px 3px rgba(0,0,0,.35)}
.client span{font-family:'Open Sans',sans-serif;font-size:13px;margin-top:28px}
.footer-links{left:137px;top:1015px;font-size:13.5px;color:var(--white)}
.footer-links a{color:var(--white);text-decoration:none}
.footer-links i{font-style:normal;margin:0 8px}
.newsletter{left:134px;top:1054px;display:flex;align-items:center}
.newsletter .icon{width:34px;height:34px;border-radius:50%;background:var(--navy-deep);border:2px solid var(--white);display:flex;align-items:center;justify-content:center;position:relative;z-index:1}
.newsletter .field{width:150px;height:33px;background:var(--white);border-radius:0 4px 4px 0;margin-left:-4px;font-size:11px;color:#999;line-height:33px;padding-left:14px}
.newsletter .btn{margin-left:4px;height:33px;line-height:33px;padding:0 8px;background:var(--blue-light);color:var(--white);font-size:13.5px;border-radius:3px}
.copyright{left:134px;top:1106px;font-size:12.5px;color:var(--white)}
.address{left:796px;top:1012px;color:var(--white);font-size:13.5px;line-height:16px}
.address .row{display:flex;gap:12px;margin-bottom:12px;align-items:flex-start}
.address .row svg{flex:none;margin-top:2px}
.address b{font-weight:700;letter-spacing:.5px}
</style>
</head>
<body>
<div class="abs header"></div>
<div class="abs follow">Follow Us :
  <span class="social" role="img" aria-label="Social network link"></span>
  <span class="social" role="img" aria-label="Social network link"></span>
  <span class="social" role="img" aria-label="Social network link"></span>
</div>
<div class="abs logo"><span class="mark"></span><span class="name">TorvelCapital</span></div>
<div class="abs contact-top">
  <div class="ring"><svg width="20" height="20" viewBox="0 0 24 24"><path d="M6.6 10.8a15 15 0 0 0 6.6 6.6l2.2-2.2a1 1 0 0 1 1-.25 11.4 11.4 0 0 0 3.6.57 1 1 0 0 1 1 1V20a1 1 0 0 1-1 1A17 17 0 0 1 3 4a1 1 0 0 1 1-1h3.5a1 1 0 0 1 1 1c0 1.25.2 2.45.57 3.57a1 1 0 0 1-.25 1z" fill="#444"/></svg></div>
  <div><div class="q">Have A Question ?</div><div class="num">555-310-2287</div></div>
</div>

<div class="abs backdrop"></div>
<div class="abs footer-band"></div>
<div class="abs page"></div>

<nav class="abs nav"><ul>
  <li class="active">Home</li><li>About</li><li>Services</li><li>Current Engagements</li><li>Completed Transactions</li><li style="border:none">Contact Us</li>
</ul></nav>

<div class="abs hero" role="img" aria-label="Photograph of a hand moving a chess piece against a blue sky"></div>
<div class="abs hero-caption">
  <h1>Torvel Capital LLC Is</h1>
  <p>Dallas-based private investment banking advisory firm that acts as an intermediary on behalf of buyers &amp; sellers of private companies.</p>
</div>

<section class="abs about">
  <h2 class="col-head">About <span>Torvel</span>Capital</h2>
  <div class="photo" role="img" aria-label="Photograph of business people meeting around a table"></div>
  <p>Torvel Capital's history in mergers and acquisitions traces back to 1998. We pride our selves in successfully matching buyers with sellers and enabling shareholders of all .</p>
  <div class="more">Read More »</div>
</section>
<div class="abs divider" style="left:433px;top:700px"></div>

<section class="abs services">
  <h2 class="col-head">What <span>We Do</span></h2>
  <div class="svc"><svg width="40" height="32" viewBox="0 0 40 32"><path d="M3 14l8-7 7 2 6-2 8 4 5 3-8 9-6 3-7-4-7-4z" fill="none" stroke="#666" stroke-width="2.5"/></svg>Buy-Side Acquisitions</div>
  <div class="svc" style="height:74px"><svg width="40" height="34" viewBox="0 0 40 34"><rect x="2" y="22" width="5" height="10" fill="#666"/><rect x="10" y="17" width="5" height="15" fill="#666"/><rect x="18" y="12" width="5" height="20" fill="#666"/><rect x="26" y="7" width="5" height="25" fill="#666"/><path d="M2 18l12-8 8 3 10-9" stroke="#666" stroke-width="2" fill="none"/></svg>Recapitalizations &amp;<br>Growth Capital Partnerships</div>
  <div class="svc" style="border:none"><svg width="40" height="34" viewBox="0 0 40 34"><text x="12" y="14" font-family="Lato,sans-serif" font-weight="700" font-size="16" fill="#666">$</text><path d="M2 22h10l6 3h10l-3 5H4z" fill="#666"/></svg>Sell-Side Transactions</div>
  <div class="more">Read More »</div>
</section>
<div class="abs divider" style="left:753px;top:700px"></div>

<section class="abs testimonials">
  <h2 class="col-head">Client <span>Testimonials</span></h2>
  <div class="bubble"><span style="font-style:normal;font-size:30px;color:#c4c6c9;line-height:0;vertical-align:-10px">“</span> Duis autem vel eum iriureol hder in a vultat velit esse moles conqat vela ilu adipsin &nbsp;feugiat.Duis autem vel eum ure hendrern vultat velit esse autm vel eum iriure dol</div>
  <div class="client"><div class="avatar" role="img" aria-label="Client portrait"></div><span>Mr. Dolore Eu Feugiat</span></div>
  <div class="more">Read More »</div>
</section>

<div class="abs footer-links"><a href="#">Home</a><i>|</i><a href="#">About</a><i>|</i><a href="#">Services</a><i>|</i><a href="#">Current Engagements</a><i>|</i><a href="#">Completed Transactions</a><i>|</i><a href="#">Contact Us</a></div>
<div class="abs newsletter">
  <div class="icon"><svg width="16" height="12" viewBox="0 0 16 12"><rect x="0.5" y="0.5" width="15" height="11" fill="none" stroke="#fff"/><path d="M1 1l7 6 7-6" stroke="#fff" fill="none"/></svg></div>
  <div class="field">Sign Up for Newsletter</div>
  <div class="btn">SUBSCRIBE</div>
</div>
<div class="abs copyright">© Copyright 2014 Torvel Capital. | All Rights Reserved</div>

<div class="abs address">
  <div class="row"><svg width="12" height="18" viewBox="0 0 12 18"><path d="M6 0a6 6 0 0 1 6 6c0 4-6 12-6 12S0 10 0 6a6 6 0 0 1 6-6z" fill="#fff"/><circle cx="6" cy="6" r="2.3" fill="#0b3572"/></svg><div>Hong Kong: Room 1804 Harbourline Tower<br>12 - 18 Kingsmere Road East<br>Eastbay, Hong Kong</div></div>
  <div class="row"><svg width="16" height="14" viewBox="0 0 24 24"><path d="M6.6 10.8a15 15 0 0 0 6.6 6.6l2.2-2.2a1 1 0 0 1 1-.25 11.4 11.4 0 0 0 3.6.57 1 1 0 0 1 1 1V20a1 1 0 0 1-1 1A17 17 0 0 1 3 4a1 1 0 0 1 1-1h3.5a1 1 0 0 1 1 1c0 1.25.2 2.45.57 3.57a1 1 0 0 1-.25 1z" fill="#fff"/></svg><b>555-310-2287</b></div>
  <div class="row"><svg width="16" height="12" viewBox="0 0 16 12"><rect width="16" height="12" fill="#fff"/><path d="M1 1l7 6 7-6" stroke="#0b3572" fill="none"/></svg><span style="letter-spacing:.5px">info@torvelcapital.com</span></div>
</div>
</body>
</html>
```